Site for entrepreneurs/small businesses needs Logo, Homepage

Looking for a logo, either an icon, or stylized text, or a combination of both, and a home page design which fits with it. The logo will be for use on the public website as well as for printed collateral (business cards, post cards, brochures and various other marketing materials).

The site is called Orbitwell (Orbitwell.example). This is to be a national, and eventually an international brand. The new service will provide an easy-to-use platform for entrepreneurs to build their business and web presence together in an integrated way which allows them to focus on their core competency.

The site/service will be dead-simple to use, A/B/C, 1/2/3. We will want some sort of "Get started for FREE" promotional space to collect the person's email address with multiple points of interest which guide the user back to this one call to action: sign up for free. We will feature editorial/blog stories, customer testimonials, and present several key features the the reader just can't live without if they are starting a new business.

Criteria:
* Refer to our comparable sites/logos in the design document attached
* Incorporate our color scheme (but complementary colors welcome)
* No Serif fonts!
* No photo-realistic elements for logo
* Logo must present well in gray scale and/or black/white (for printed materials)
* Strokes/borders that are wider to promote simplicity (vs. thin/precise lines which promote technical complexity)

Inspirations:
* Creative/Custom (but legible) fonts
* Excitement, energetic, jumping for joy
* Karate / Ninja / Power / Precision
* Dance Moves
* Regional influences: California, Silicon Valley, West Coast, Surf City, Beaches, Sunset
* Simple/easy, no-brainer solutions

Target Market(s)

Small Businesses / Entrepreneurs

Logo Text

Orbitwell or Orbitwell.example

Number of Pages Required

1 page

Font styles to use
Sans Serif
Decorative

Requirements
Must have
• See the attached style guide (PDF)

```html
<!DOCTYPE html>
<html lang="en">
<head>
<meta charset="utf-8">
<title>Orbitwell — Home</title>
<link href="https://fonts.googleapis.com/css2?family=Roboto:ital,wght@0,400;0,500;0,700;0,900;1,400&display=swap" rel="stylesheet">
<style>
:root{
  --blue-deep:#0b2f8f;
  --blue:#1a5fd0;
  --blue-line:#3a6cc0;
  --orange:#f08a0c;
  --orange-2:#f5a623;
  --ink:#1d2540;
  --text:#55596a;
  --cream:#f3efe8;
  --purple:#4f0c96;
  --purple-2:#5e14a8;
  --mist:#dfe9eb;
  --teal:#3aa6b8;
  --white:#ffffff;
}
*{margin:0;padding:0;box-sizing:border-box}
html,body{width:1200px;height:4500px;overflow:hidden}
body{font-family:"Roboto",Arial,sans-serif;color:var(--text);background:var(--white);position:relative}
section,header,footer{position:absolute;left:0;width:1200px}
.abs{position:absolute}

/* hero */
.hero{top:0;height:790px;background:linear-gradient(160deg,var(--blue-deep) 0%,#0f45b5 45%,var(--blue) 100%);overflow:hidden}
.brand{left:135px;top:52px;display:flex;align-items:center;gap:10px;color:var(--white);font-weight:700;font-size:30px}
.brand-dot{width:30px;height:30px;border-radius:50%;background:var(--white)}
.nav{left:452px;top:64px;display:flex;gap:26px;font-size:14px;font-weight:500;color:var(--white);letter-spacing:.3px;align-items:center}
.nav .signin{border:2px solid var(--white);border-radius:16px;padding:5px 16px;margin-left:12px}
.hero h1{left:128px;top:262px;color:var(--white);font-size:46px;font-weight:700;line-height:58px;letter-spacing:1px}
.hero p.lead{left:130px;top:398px;width:450px;color:#e6edff;font-size:13px;line-height:20px}
.btn-outline{left:130px;top:496px;border:2px solid var(--white);border-radius:18px;color:var(--white);font-size:13px;font-weight:700;padding:8px 18px}
.dots{left:134px;top:566px;display:flex;gap:8px}
.dots i{width:9px;height:9px;border-radius:50%;background:var(--white);display:block}
.dots i:first-child{box-shadow:0 0 0 3px rgba(255,255,255,.4)}
.hero-art{left:610px;top:185px;width:460px;height:450px;border-radius:30px;background:radial-gradient(circle at 50% 45%,#3fd2ff 0%,#1d8de6 45%,rgba(26,95,208,0) 75%)}
.hero-edge{left:0;top:690px}

/* get started */
.getstarted{top:780px;height:120px;background:var(--cream)}
.getstarted h2{left:128px;top:45px;font-size:26px;font-weight:700;color:#2b2b3a}
.field{top:40px;width:220px;height:40px;border-radius:20px;background:var(--white);border:1px solid #e3ddd3;font-size:12px;color:#888;padding:12px 18px}
.btn-orange{background:linear-gradient(90deg,var(--orange),var(--orange-2));color:var(--white);font-weight:700;font-size:13px;border-radius:20px;text-align:center}
.getstarted .btn-orange{left:910px;top:40px;width:160px;height:40px;line-height:40px}

/* features */
.features{top:900px;height:840px}
.section-title{width:1200px;text-align:center;font-size:32px;font-weight:700;color:var(--ink);letter-spacing:1px}
.features .section-title{top:130px}
.features .intro{left:150px;top:190px;width:900px;text-align:center;font-size:13px;line-height:22px}
.feature{width:290px;display:flex;gap:20px}
.feature .icon{flex:none;width:80px;height:80px;border:2px solid var(--blue-line);border-radius:50%;display:flex;align-items:center;justify-content:center}
.feature h3{font-size:16px;font-weight:500;color:var(--ink);line-height:24px;margin-bottom:10px}
.feature p{font-size:12px;line-height:20px}

/* testimonials */
.testimonials{top:1740px;height:820px}
.testimonials .section-title{top:165px;color:var(--white)}
.quote{width:278px;height:160px;top:335px;background:var(--white);border-radius:14px;padding:52px 24px 0;text-align:center;font-size:12px;font-style:italic;line-height:20px;color:#4a4a5a}
.avatar{width:84px;height:84px;border-radius:50%;top:290px;border:4px solid var(--white);background:linear-gradient(135deg,#c9a58a,#6b4a3a)}
.who{width:278px;top:528px;text-align:center;color:var(--white);font-size:15px;font-weight:500}
.stars{width:278px;top:560px;text-align:center;color:var(--white);font-size:14px;letter-spacing:5px}

/* build */
.build{top:2560px;height:635px}
.build h2{left:130px;top:160px;font-size:33px;font-weight:700;color:var(--ink);line-height:44px}
.build p{left:130px;top:270px;width:490px;font-size:14px;line-height:24px}
.build .btn-orange{left:130px;top:415px;width:138px;height:38px;line-height:38px}
.build-art{left:625px;top:75px;width:420px;height:420px;border-radius:50%;background:radial-gradient(circle,#d9d7fb 0%,#ecebfc 60%,#f3f2fd 100%)}

/* blog */
.blog{top:3195px;height:830px;background:var(--mist)}
.blog .section-title{top:90px}
.rule{left:570px;top:168px;width:60px;height:3px;background:var(--blue-line)}
.post{width:295px;background:var(--white);border-radius:4px;box-shadow:0 2px 10px rgba(0,0,0,.08);overflow:hidden}
.post .thumb{height:180px;background:linear-gradient(180deg,#5cc0cf,var(--teal))}
.post .body{padding:22px 18px 24px}
.post .date{font-size:12px;color:#444;display:flex;gap:8px;align-items:center}
.post h3{margin-top:16px;font-size:13px;font-weight:700;color:#1f3a7a;line-height:22px;text-transform:uppercase}
.post p{margin-top:12px;font-size:12px;line-height:20px}

/* footer */
.site-footer{top:4025px;height:475px;background:var(--white)}
.site-footer h4{font-size:15px;font-weight:700;color:var(--ink);letter-spacing:.5px}
.col{top:95px}
.col p,.col li{font-size:11px;line-height:20px;color:#444}
.col ul{list-style:none;margin-top:20px}
.col ul li::before{content:"";display:inline-block;width:4px;height:4px;background:#444;border-radius:50%;margin-right:8px;vertical-align:middle}
.newsletter-field{margin-top:14px;width:275px;height:34px;border:1px solid #ddd;font-size:11px;color:#999;padding:9px 12px}
.col .btn-orange{margin-top:14px;width:110px;height:32px;line-height:32px;border-radius:2px;font-size:12px}
.contact-item{display:flex;gap:12px;align-items:flex-start;margin-top:16px;font-size:11px;line-height:18px;color:#444}
.social-item{display:flex;gap:10px;align-items:center;margin-top:8px;font-size:11px;color:#444}
.social-item i{width:22px;height:22px;border:2px solid #555;border-radius:50%;display:block}
.legal{left:0;top:365px;width:1200px;border-top:1px solid #e6e6e6;padding-top:52px;text-align:center;font-size:12px;color:#333}
</style>
</head>
<body>

<header class="hero">
  <div class="abs brand"><span class="brand-dot"></span>Orbitwell</div>
  <nav class="abs nav">
    <span>HOME</span><span>ABOUT</span><span>SERVICES</span><span>BLOG</span><span>PRICING</span><span>CONTACT US</span><span class="signin">SIGN IN</span>
  </nav>
  <h1 class="abs">QUIS AUTEM VEL<br>EUM IURE</h1>
  <p class="abs lead">Duis aute irure dolor in reprehenderit in voluptate velit esse cillum dolore eu fugiat nulla pariatur. Excepteur sint occaecat cupidatat non proident, sunt</p>
  <span class="abs btn-outline">READ MORE</span>
  <div class="abs dots"><i></i><i></i><i></i><i></i></div>
  <div class="abs hero-art" role="img" aria-label="Isometric illustration of a cloud linked to a laptop, monitor and data screens"></div>
  <svg class="abs hero-edge" width="1200" height="100" viewBox="0 0 1200 100">
    <polygon points="0,25 700,68 1200,58 1200,100 0,100" fill="#f08a0c"/>
    <polygon points="0,70 1200,80 1200,100 0,100" fill="#f3efe8"/>
  </svg>
</header>

<section class="getstarted">
  <h2 class="abs">GET STARTED FOR FREE</h2>
  <div class="abs field" style="left:430px">Email</div>
  <div class="abs field" style="left:668px">Name</div>
  <div class="abs btn-orange">SIGN UP FOR FREE</div>
</section>

<section class="features">
  <h2 class="abs section-title">KEY FEATURES</h2>
  <p class="abs intro">Sed ut perspiciatis unde omnis iste natus error sit voluptatem accusantium doloremque laudantium, totam rem aperiam, eaque ipsa quae ab illo inventore veritatis et quasi architecto beatae vitae dicta sunt explicabo. Nemo enim ipsam voluptatem</p>

  <div class="abs feature" style="left:135px;top:305px">
    <div class="icon"><svg width="36" height="36" viewBox="0 0 36 36" fill="none" stroke="#3a6cc0" stroke-width="2.5"><rect x="4" y="6" width="28" height="19" rx="2"/><path d="M13 31h10M18 25v6"/></svg></div>
    <div><h3>Quis autem vel eum<br>iure reprehenderit</h3><p>Sed ut perspiciatis unde omnis iste natus error sit voluptatem accusantium doloremque rdum, totam rem aperiam</p></div>
  </div>
  <div class="abs feature" style="left:457px;top:305px">
    <div class="icon"><svg width="36" height="36" viewBox="0 0 36 36" fill="none" stroke="#3a6cc0" stroke-width="2.5"><circle cx="18" cy="18" r="3"/><ellipse cx="18" cy="18" rx="14" ry="6"/><ellipse cx="18" cy="18" rx="14" ry="6" transform="rotate(60 18 18)"/><ellipse cx="18" cy="18" rx="14" ry="6" transform="rotate(120 18 18)"/></svg></div>
    <div><h3>Quis autem vel eum<br>iure reprehenderit</h3><p>Sed ut perspiciatis unde omnis iste natus error sit voluptatem accusantium doloremque rdum, totam rem aperiam</p></div>
  </div>
  <div class="abs feature" style="left:785px;top:305px">
    <div class="icon"><svg width="36" height="36" viewBox="0 0 36 36" fill="none" stroke="#3a6cc0" stroke-width="2.5"><circle cx="18" cy="18" r="14"/><ellipse cx="18" cy="18" rx="6" ry="14"/><path d="M4 18h28"/></svg></div>
    <div><h3>Quis autem vel eum<br>iure reprehenderit</h3><p>Sed ut perspiciatis unde omnis iste natus error sit voluptatem accusantium doloremque rdum, totam rem aperiam</p></div>
  </div>
  <div class="abs feature" style="left:135px;top:515px">
    <div class="icon"><svg width="36" height="36" viewBox="0 0 36 36" fill="#3a6cc0"><ellipse cx="18" cy="8" rx="11" ry="4"/><path d="M7 11c0 2 5 4 11 4s11-2 11-4v5c0 2-5 4-11 4S7 18 7 16zM7 19c0 2 5 4 11 4s11-2 11-4v5c0 2-5 4-11 4S7 26 7 24z"/></svg></div>
    <div><h3>Quis autem vel eum<br>iure reprehenderit</h3><p>Sed ut perspiciatis unde omnis iste natus error sit voluptatem accusantium doloremque rdum, totam rem aperiam</p></div>
  </div>
  <div class="abs feature" style="left:457px;top:515px">
    <div class="icon"><svg width="36" height="36" viewBox="0 0 36 36" fill="none" stroke="#3a6cc0" stroke-width="2.5"><path d="M9 22a7 7 0 0 1 2-13 9 9 0 0 1 16 3 5 5 0 0 1 0 10z"/><path d="M12 26h12M14 30h8"/></svg></div>
    <div><h3>Quis autem vel eum<br>iure reprehenderit</h3><p>Sed ut perspiciatis unde omnis iste natus error sit voluptatem accusantium doloremque rdum, totam rem aperiam</p></div>
  </div>
  <div class="abs feature" style="left:785px;top:515px">
    <div class="icon"><svg width="36" height="36" viewBox="0 0 36 36" fill="none" stroke="#3a6cc0" stroke-width="2.5"><path d="M5 5v26h26"/><path d="M9 25l7-8 5 4 9-11"/></svg></div>
    <div><h3>Quis autem vel eum<br>iure reprehenderit</h3><p>Sed ut perspiciatis unde omnis iste natus error sit voluptatem accusantium doloremque rdum, totam rem aperiam</p></div>
  </div>
</section>

<section class="testimonials">
  <svg class="abs" style="left:0;top:0" width="1200" height="820" viewBox="0 0 1200 820">
    <defs><linearGradient id="purpleFill" x1="0" y1="0" x2="0" y2="1"><stop offset="0" stop-color="#4f0c96"/><stop offset="1" stop-color="#5e14a8"/></linearGradient></defs>
    <polygon points="0,90 615,0 1200,90 1200,820 0,820" fill="url(#purpleFill)"/>
    <g fill="#ffffff">
      <ellipse cx="80" cy="790" rx="180" ry="60"/><ellipse cx="300" cy="770" rx="160" ry="50"/>
      <ellipse cx="520" cy="780" rx="170" ry="55"/><ellipse cx="760" cy="760" rx="160" ry="60"/>
      <ellipse cx="980" cy="775" rx="170" ry="55"/><ellipse cx="1160" cy="770" rx="140" ry="55"/>
      <rect x="0" y="790" width="1200" height="30"/>
    </g>
  </svg>
  <h2 class="abs section-title">CUSTOMER TESTIMONIALS</h2>

  <div class="abs quote" style="left:152px">“ Quis autem vel eum iure reprehenderit qui in ea voluptate velit esse quam nihil molestiae consequatur, vel illum qui dolorem eum fugiat quo voluptas</div>
  <div class="abs avatar" role="img" aria-label="Customer portrait" style="left:249px"></div>
  <div class="abs who" style="left:152px">Dana - Orbitwell</div>
  <div class="abs stars" style="left:152px">★★★★★</div>

  <div class="abs quote" style="left:462px">“ Quis autem vel eum iure reprehenderit qui in ea voluptate velit esse quam nihil molestiae consequatur, vel illum qui dolorem eum fugiat quo voluptas</div>
  <div class="abs avatar" role="img" aria-label="Customer portrait" style="left:559px"></div>
  <div class="abs who" style="left:462px">Dana - Orbitwell</div>
  <div class="abs stars" style="left:462px">★★★★★</div>

  <div class="abs quote" style="left:772px">“ Quis autem vel eum iure reprehenderit qui in ea voluptate velit esse quam nihil molestiae consequatur, vel illum qui dolorem eum fugiat quo voluptas</div>
  <div class="abs avatar" role="img" aria-label="Customer portrait" style="left:869px"></div>
  <div class="abs who" style="left:772px">Dana - Orbitwell</div>
  <div class="abs stars" style="left:772px">★★★★★</div>
</section>

<section class="build">
  <h2 class="abs">BUILD PRODUCTS<br>APPS AND SERVICES</h2>
  <p class="abs">Sed ut perspiciatis unde omnis iste natus error sit voluptatem accusantium doloremque laudantium, totam rem aperiam, eaque ipsa quae ab illo inventore veritatis et quasi architecto beatae vitae dicta sunt explicabo. Nemo enim ipsam voluptatem quia voluptas sit aspernatur</p>
  <div class="abs btn-orange">READ MORE</div>
  <div class="abs build-art" role="img" aria-label="Illustration of a team working with laptops around a product board"></div>
</section>

<section class="blog">
  <h2 class="abs section-title">LATEST BLOG</h2>
  <div class="abs rule"></div>

  <article class="abs post" style="left:133px;top:280px">
    <div class="thumb" role="img" aria-label="Illustration of people climbing toward a goal"></div>
    <div class="body">
      <div class="date"><svg width="12" height="12" viewBox="0 0 12 12" fill="#1f3a7a"><rect x="0" y="2" width="12" height="10" rx="1"/></svg>October 17, 2018</div>
      <h3>Quis autem vel eum iure reprehen derit qui in ea voluptate</h3>
      <p>Sed ut perspiciatis unde omnis iste natus error sit voluptatem accusantium doloremque latium, totam rem aperiam</p>
    </div>
  </article>
  <article class="abs post" style="left:455px;top:240px">
    <div class="thumb" role="img" aria-label="Illustration of a person at a desk surrounded by floating notes"></div>
    <div class="body">
      <div class="date"><svg width="12" height="12" viewBox="0 0 12 12" fill="#1f3a7a"><rect x="0" y="2" width="12" height="10" rx="1"/></svg>October 17, 2018</div>
      <h3>Quis autem vel eum iure reprehen derit qui in ea voluptate</h3>
      <p>Sed ut perspiciatis unde omnis iste natus error sit voluptatem accusantium doloremque latium, totam rem aperiam</p>
    </div>
  </article>
  <article class="abs post" style="left:775px;top:280px">
    <div class="thumb" role="img" aria-label="Illustration of a team meeting around a chart board"></div>
    <div class="body">
      <div class="date"><svg width="12" height="12" viewBox="0 0 12 12" fill="#1f3a7a"><rect x="0" y="2" width="12" height="10" rx="1"/></svg>October 17, 2018</div>
      <h3>Quis autem vel eum iure reprehen derit qui in ea voluptate</h3>
      <p>Sed ut perspiciatis unde omnis iste natus error sit voluptatem accusantium doloremque latium, totam rem aperiam</p>
    </div>
  </article>

  <svg class="abs" style="left:0;top:740px" width="1200" height="90" viewBox="0 0 1200 90">
    <g fill="#ffffff">
      <ellipse cx="90" cy="85" rx="200" ry="45"/><ellipse cx="380" cy="75" rx="180" ry="45"/>
      <ellipse cx="640" cy="80" rx="190" ry="40"/><ellipse cx="900" cy="70" rx="180" ry="45"/>
      <ellipse cx="1140" cy="75" rx="170" ry="45"/>
    </g>
  </svg>
</section>

<footer class="site-footer">
  <div class="abs col" style="left:130px;width:290px">
    <h4>SIGN UP FOR NEWSLETTER</h4>
    <p style="margin-top:16px">Excepteur sint occaecat cupidatat non proident, sunt in culpa qui officia deserunt</p>
    <div class="newsletter-field">Enter email</div>
    <div class="btn-orange">SIGN UP</div>
  </div>
  <div class="abs col" style="left:468px;width:260px">
    <h4>CONTACT US</h4>
    <div class="contact-item" style="margin-top:22px"><svg width="14" height="16" viewBox="0 0 14 16" fill="#f08a0c"><path d="M7 0a6 6 0 0 1 6 6c0 4-6 10-6 10S1 10 1 6a6 6 0 0 1 6-6z"/><circle cx="7" cy="6" r="2" fill="#fff"/></svg><span>Orbitwell<br>Lakeview, Ohio 4500-1200</span></div>
    <div class="contact-item"><svg width="14" height="14" viewBox="0 0 14 14" fill="#f08a0c"><path d="M3 0l3 3-2 2c1 2 3 4 5 5l2-2 3 3-2 3C6 14 0 8 0 3z"/></svg><span>Phone: (555) 010-4821</span></div>
    <div class="contact-item"><svg width="14" height="12" viewBox="0 0 14 12" fill="#f08a0c"><rect width="14" height="12" rx="1"/><path d="M1 1l6 5 6-5" stroke="#fff" fill="none"/></svg><span>Email: info@orbitwell.example</span></div>
  </div>
  <div class="abs col" style="left:770px">
    <h4>QUICK LINKS</h4>
    <ul><li>Home</li><li>About</li><li>Services</li><li>Blog</li><li>Pricing</li><li>Contact Us</li></ul>
  </div>
  <div class="abs col" style="left:970px">
    <h4>SOCIAL</h4>
    <div style="margin-top:14px">
      <div class="social-item"><i></i>Newsfeed</div>
      <div class="social-item"><i></i>Microblog</div>
      <div class="social-item"><i></i>Circles</div>
      <div class="social-item"><i></i>Videos</div>
    </div>
  </div>
  <div class="abs legal">© Copyright 2018 Orbitwell. All Rights Reserved.</div>
</footer>

</body>
</html>
```